Business Card Design for Flood Rescue 360 - Property Restoration Professionals

I need a business card designed for Flood Rescue 360. We are a full-service property restoration solution. Providing water, fire, smoke & storm restoration as well as mold remediation and full remodel or reconstruction to homes and businesses across Dallas-Fort Worth, TX.
Target Market(s)
home and business owners with insurance covered property damage from water, fire or storm related damage
Industry/Entity Type
property restoration
Contact Information for Business Card
Marcus Pelley General Manager Cell: 214-555-0193 Office: 469-555-0148 email: Marcus@FloodRescue360.example services: Water, Fire, Mold, Reconstruction Tagline: Fast Help When the Water Rises!
Look and feel
Each slider illustrates characteristics of the customer's brand and the style your logo design should communicate.

```html
<!DOCTYPE html>
<html lang="en">
<head>
<meta charset="utf-8">
<title>Flood Rescue 360 – Business Card</title>
<link href="https://fonts.googleapis.com/css2?family=Montserrat:wght@400;600;700&family=Oswald:wght@500;600&display=swap" rel="stylesheet">
<style>
  :root {
    --brand-blue: #12b2e6;
    --ink: #1c1c1c;
    --card-black: #202122;
    --stage: #3a3b3d;
    --band-grey: #7a7b7c;
    --paper: #ffffff;
  }
  * { margin: 0; padding: 0; box-sizing: border-box; }
  html, body { width: 1200px; height: 1200px; overflow: hidden; }
  body {
    background: var(--stage);
    font-family: "Montserrat", sans-serif;
    display: flex;
    flex-direction: column;
    align-items: center;
    justify-content: center;
    gap: 60px;
  }
  .card {
    position: relative;
    width: 900px;
    height: 514px;
    border-radius: 36px;
    overflow: hidden;
  }

  /* Front side */
  .card-front { background: var(--paper); }
  .front-band {
    position: absolute; left: 0; bottom: 0;
    height: 30px; width: 610px;
    background: var(--brand-blue);
  }
  .front-band-grey {
    position: absolute; right: 0; bottom: 0;
    height: 46px; width: 276px;
    background: var(--band-grey);
  }
  .person { position: absolute; left: 70px; top: 250px; }
  .person-name {
    color: var(--brand-blue);
    font-weight: 600;
    font-size: 40px;
    letter-spacing: 1px;
    line-height: 1;
  }
  .person-title {
    color: var(--ink);
    font-weight: 400;
    font-size: 22px;
    letter-spacing: 1px;
    margin-top: 2px;
  }
  .contact-list {
    position: absolute; left: 80px; top: 350px;
    list-style: none;
  }
  .contact-list li {
    display: flex; align-items: center;
    gap: 18px;
    font-size: 24px;
    color: var(--ink);
    height: 40px;
  }
  .contact-list svg { width: 26px; height: 26px; fill: var(--brand-blue); }
  .contact-list .email { font-size: 21px; letter-spacing: -0.3px; }

  .wordmark {
    display: flex; align-items: center;
    color: var(--brand-blue);
    font-weight: 600;
    white-space: nowrap;
  }
  .wordmark-dot {
    border-radius: 50%;
    background: var(--brand-blue);
    flex: none;
  }
  .front-wordmark {
    position: absolute; left: 520px; top: 110px;
    font-size: 36px; gap: 14px;
  }
  .front-wordmark .wordmark-dot { width: 22px; height: 22px; }

  .services {
    position: absolute; left: 580px; top: 220px;
    font-family: "Oswald", sans-serif;
    text-transform: uppercase;
  }
  .services-label {
    color: var(--brand-blue);
    font-weight: 500;
    font-size: 24px;
    letter-spacing: 0.5px;
  }
  .services ul { list-style: none; margin-left: 14px; }
  .services li {
    color: var(--ink);
    font-weight: 600;
    font-size: 27px;
    line-height: 1.15;
    display: flex; align-items: center; gap: 10px;
  }
  .services li::before {
    content: ""; width: 9px; height: 9px; border-radius: 50%;
    background: var(--brand-blue);
  }

  /* Back side */
  .card-back {
    background: var(--card-black);
    border-bottom: 3px solid var(--brand-blue);
  }
  .back-wordmark {
    position: absolute; left: 0; right: 0; top: 190px;
    justify-content: center;
    font-size: 66px; gap: 24px;
  }
  .back-wordmark .wordmark-dot { width: 40px; height: 40px; }
  .tagline {
    position: absolute; left: 0; right: 0; bottom: 80px;
    text-align: center;
    color: var(--brand-blue);
    font-weight: 700;
    font-size: 30px;
    letter-spacing: 1px;
  }
</style>
</head>
<body>

  <section class="card card-front" aria-label="Business card front">
    <div class="wordmark front-wordmark">
      <span class="wordmark-dot" aria-hidden="true"></span>
      <span>Flood Rescue 360</span>
    </div>

    <div class="services">
      <div class="services-label">Services:</div>
      <ul>
        <li>Water</li>
        <li>Fire</li>
        <li>Mold</li>
        <li>Reconstruction</li>
      </ul>
    </div>

    <div class="person">
      <div class="person-name">MARCUS PELLEY</div>
      <div class="person-title">GENERAL MANAGER</div>
    </div>

    <ul class="contact-list">
      <li>
        <svg viewBox="0 0 24 24" aria-hidden="true"><path d="M7 1h10a2 2 0 0 1 2 2v18a2 2 0 0 1-2 2H7a2 2 0 0 1-2-2V3a2 2 0 0 1 2-2zm0 3v14h10V4H7zm5 15.5a1 1 0 1 0 0 2 1 1 0 0 0 0-2z"/></svg>
        <span>214-555-0193</span>
      </li>
      <li>
        <svg viewBox="0 0 24 24" aria-hidden="true"><path d="M6.6 10.8a15.1 15.1 0 0 0 6.6 6.6l2.2-2.2a1 1 0 0 1 1-.25 11.4 11.4 0 0 0 3.6.57 1 1 0 0 1 1 1V20a1 1 0 0 1-1 1A17 17 0 0 1 3 4a1 1 0 0 1 1-1h3.5a1 1 0 0 1 1 1c0 1.25.2 2.450.57 3.6a1 1 0 0 1-.25 1z"/></svg>
        <span>469-555-0148</span>
      </li>
      <li>
        <svg viewBox="0 0 24 24" aria-hidden="true"><path d="M2 5h20v14H2V5zm2 2v.4l8 5.2 8-5.2V7H4zm0 2.8V17h16V9.8l-8 5.2-8-5.2z"/></svg>
        <span class="email">Marcus@FloodRescue360.example</span>
      </li>
    </ul>

    <div class="front-band"></div>
    <div class="front-band-grey"></div>
  </section>

  <section class="card card-back" aria-label="Business card back">
    <div class="wordmark back-wordmark">
      <span class="wordmark-dot" aria-hidden="true"></span>
      <span>Flood Rescue 360</span>
    </div>
    <div class="tagline">Fast Help When the Water Rises!</div>
  </section>

</body>
</html>
```